PostCard Design Project

I am making a mailing postcard
I am having the mailing printed using 4 color foil on certain parts.
I am looking for a design that maximizes the foil process where certain parts are done in foil to grab the customers attention (example: if there is a car on the postcard the headlights would be done in foil) .
I am targeting some industries, (auto, real estate, medical, beauty) I would like the post card to have examples of postcard ideas for 2 or 3 of these industries.
specs:
the postcard should be atleast 6.5x9 up to 8.5x11, I don't want to restrict the space for the creative as I don't want everything to look like a huge mess. both sides will be used.
the piece is a direct mail piece so it has to meet requirements of https://www.mailvantor.com/business/pdf/quick-reference-guide.pdf
text will be
"business with no limits, meet mailing with no addresses, gain new customers through "Open Porch Route Drop" reach new customers at their home without needing their address. "
I also want some current print specials I am running included.
-double your order FREE (order 500 business cards and get 1000)
-250 100lb gloss stock brochures 99.00
-business packages (cards, envelopes and letterhead) 299
-1000 flyers 140.40
-5000 postcards 179.99
A list of services
banners
booklets
brochures
business cards
calendars
catalogs
CD/DVD packages
envelopes
event tickets
flyers
hangtags
postcards
posters
presentation folders
rack cards
labels
table tents
window cling and decal
"order 24/7 orders@inkwillow.com" must be included
my logo is InkWillow will be supplied later
ive received some great designs. however Im looking for something a little more modern like some zorvel would put out. if the amount of words is too much please feel free to edit. also an idea i had for the list of services i offer is to have it transparent yet readable as the background of the postcard some small some big but covering the entire backgroud. you can then design on top of that with other thing. just an early morning thought
Reason: I have uploaded a sketch of my idea, please take time to look at it for an accurate depiction of what im looking for. feel free to add elements that make it pop off the page
Reason: We are getting close i will be providing feed back today

```html
<!DOCTYPE html>
<html lang="en">
<head>
<meta charset="utf-8">
<title>InkWillow Mailer Postcard</title>
<link rel="stylesheet" href="https://fonts.googleapis.com/css2?family=Arimo:wght@400;700&family=Cabin:wght@500;600&display=swap">
<style>
  :root {
    --board-light: #eef1dc;
    --board-mid: #c9d3a6;
    --board-dark: #a9b985;
    --card: #231f20;
    --white: #ffffff;
    --ink: #111111;
    --red: #e3201b;
    --shine: #c8102e;
    --orange: #f7a22d;
    --orange-text: #f39a21;
    --logo-blue: #3a8fd6;
  }
  * { box-sizing: border-box; margin: 0; padding: 0; }
  html, body { width: 904px; height: 1200px; overflow: hidden; }
  body {
    position: relative;
    font-family: "Arimo", Arial, sans-serif;
    background: radial-gradient(ellipse at 50% 50%, var(--board-light) 0%, var(--board-mid) 70%, var(--board-dark) 100%);
  }
  .card {
    position: absolute;
    left: 86px;
    width: 714px;
    height: 514px;
    background: var(--card);
    color: var(--white);
  }
  .card--front { top: 76px; }
  .card--back { top: 607px; }

  /* Front */
  .headline {
    position: absolute; left: 40px; top: 18px;
    font-family: "Cabin", "Arimo", sans-serif; font-weight: 500;
    font-size: 43px; letter-spacing: 0.5px;
  }
  .shine {
    position: absolute; left: 40px; top: 78px;
    font-family: "Arimo", sans-serif; font-weight: 700;
    font-size: 78px; color: var(--shine);
    -webkit-text-stroke: 2px var(--white);
    letter-spacing: 2px;
  }
  .hours, .order-email {
    position: absolute; left: 40px;
    font-family: "Cabin", "Arimo", sans-serif; font-weight: 500;
    color: var(--orange-text); font-size: 33px;
  }
  .hours { top: 182px; }
  .order-email { top: 217px; }
  .logo-box {
    position: absolute; left: 480px; top: 81px; width: 192px; height: 61px;
    background: var(--white);
    display: flex; align-items: center; justify-content: center; gap: 10px;
  }
  .logo-box .dot { width: 26px; height: 26px; border-radius: 50%; background: var(--logo-blue); }
  .logo-box .name { font-family: "Arimo", sans-serif; font-size: 25px; color: var(--logo-blue); }
  .photo { position: absolute; }
  .photo--smile {
    left: 440px; top: 163px; width: 246px; height: 157px;
    border: 6px solid var(--orange);
    background: linear-gradient(90deg, #d98f86 0%, #f6ede9 45%, #f6ede9 55%, #d98f86 100%);
  }
  .photo--beauty {
    left: 157px; top: 335px; width: 244px; height: 156px;
    background: linear-gradient(120deg, #f5f1ef 0%, #d9b0a2 55%, #6e4c3f 100%);
  }
  .photo--car {
    left: 426px; top: 335px; width: 236px; height: 156px;
    background: linear-gradient(150deg, #e0261e 0%, #a30f0f 55%, #2a2a2a 100%);
  }

  /* Back */
  .services-title {
    position: absolute; left: 32px; top: 36px;
    font-family: "Arimo", sans-serif; font-weight: 700; font-size: 37px;
    background: linear-gradient(90deg, #f5e52a 0%, #f39a21 22%, #e3201b 40%, #c52ca8 58%, #3a8fd6 78%, #46b34a 100%);
    -webkit-background-clip: text; background-clip: text; color: transparent;
  }
  .services-list {
    position: absolute; left: 32px; top: 91px;
    list-style: none; font-size: 15px; line-height: 22.5px;
  }
  .services-list li::before {
    content: "\2022"; display: inline-block; width: 14px;
    color: var(--bullet, #46b34a); font-size: 17px;
  }
  .services-list li.no-bullet::before { content: ""; }
  .intro {
    position: absolute; left: 196px; top: 27px; width: 300px;
    font-size: 13.5px; line-height: 16.5px;
  }
  .indicia {
    position: absolute; left: 609px; top: 18px; width: 84px; height: 81px;
    background: var(--white); color: var(--ink);
    font-size: 10px; line-height: 12.5px; text-align: center;
    padding-top: 7px; border: 1px solid #999;
  }
  .indicia .retail { font-size: 9px; }
  .addressee {
    position: absolute; left: 528px; top: 118px; width: 165px; height: 81px;
    background: var(--white); color: var(--ink);
    font-size: 14px; line-height: 18px; padding: 20px 0 0 18px;
  }
  .specials-label {
    position: absolute; left: 398px; top: 140px;
    font-family: "Arimo", sans-serif; font-weight: 700;
    color: var(--orange-text); font-size: 20px; line-height: 18px;
  }
  .special {
    position: absolute; border-radius: 16px;
    display: flex; align-items: center; justify-content: center;
    text-align: center; font-weight: 700; font-size: 15px; line-height: 19px;
    padding: 8px;
  }
  .special--orange { background: var(--orange); color: var(--ink); }
  .special--red { background: var(--red); color: var(--white); }
  .special--cards { left: 230px; top: 168px; width: 154px; height: 124px; }
  .special--brochures { left: 391px; top: 210px; width: 124px; height: 111px; }
  .special--package { left: 230px; top: 299px; width: 157px; height: 122px; }
  .special--postcards { left: 395px; top: 334px; width: 120px; height: 94px; }
  .special--flyers { left: 307px; top: 421px; width: 102px; height: 60px; border-radius: 10px; }
</style>
</head>
<body>
  <section class="card card--front">
    <h1 class="headline">Let Us Help Your Business</h1>
    <p class="shine">SHINE !</p>
    <p class="hours">24 hr/ 7day</p>
    <p class="order-email">orders@inkwillow.com</p>
    <div class="logo-box"><span class="dot"></span><span class="name">InkWillow</span></div>
    <div class="photo photo--smile" role="img" aria-label="Close-up of two smiles, one with braces, for the dental industry"></div>
    <div class="photo photo--beauty" role="img" aria-label="Beauty portrait of a woman with glowing skin"></div>
    <div class="photo photo--car" role="img" aria-label="Red sports car headlight close-up"></div>
  </section>

  <section class="card card--back">
    <h2 class="services-title">Services</h2>
    <ul class="services-list">
      <li style="--bullet:#46b34a">banners</li>
      <li style="--bullet:#3ab0c9">booklets</li>
      <li style="--bullet:#2b3f9e">brochures</li>
      <li style="--bullet:#c52ca8">business cards</li>
      <li style="--bullet:#f5e52a">calendars</li>
      <li style="--bullet:#e3201b">catalogs</li>
      <li style="--bullet:#e3201b">CD/DVD packages</li>
      <li style="--bullet:#f39a21">envelopes</li>
      <li style="--bullet:#f5e52a">event tickets</li>
      <li style="--bullet:#46b34a">flyers</li>
      <li style="--bullet:#2e8b3e">hangtags</li>
      <li style="--bullet:#3ab0c9">postcards</li>
      <li style="--bullet:#3a8fd6">posters</li>
      <li class="no-bullet">presentation folders</li>
      <li style="--bullet:#2b3f9e">rackcards</li>
      <li style="--bullet:#ffffff">labels</li>
    </ul>
    <p class="intro">Business with no limits, meet mailing with no addresses, gain new customers through "Open Porch Route Drop" reach new customers at their home without needing their address.</p>
    <div class="indicia">PRSRT STD<br>ECRWSS<br>U.S.POSTAGE<br>PAID<br><span class="retail">OPRD Retail</span></div>
    <div class="addressee">Local<br>Postal Customer</div>
    <p class="specials-label">current<br>specials<br>print</p>
    <div class="special special--orange special--cards">Double your order FREE (order 500 business cards and get 1000)</div>
    <div class="special special--orange special--brochures">250 100lb gloss stock brochures 99.00</div>
    <div class="special special--red special--package">Business packages (cards, envelopes and letterhead) 299</div>
    <div class="special special--orange special--postcards">5000 postcards 179.99</div>
    <div class="special special--red special--flyers">1000 flyers 140.40</div>
  </section>
</body>
</html>
```